Sales sheet for printing and embroidery apparel items - Copper Hollow Graphics

I would like a one page flyer or sales sheet that I would use as a template to send different images of apparel we produce. I have attached examples of layouts I like.
- Ideally, it would have space for 3-5 items.
- I would like it one page only - not a folding flyer.
- Our companies name is Copper Hollow Graphics.
- This will be used for many different products and markets so I don't need wording/copy. You can use wording from the 7M9 or T58 flyer.

Colors
0054AA
0677BA
7BADD7
CADEEF
E8F1F8
00AB8E
00BBA5
67D7C9
C6EFE9
E9F9F6
FFC000
F8CF3A
FAE287
FDF2CF
FEFAEE

Requirements
Must have
• Places for between 3 and 5 images of apparel (t-shirts, hats etc)

```html
<!DOCTYPE html>
<html lang="en">
<head>
<meta charset="utf-8">
<title>Copper Hollow Graphics – Sales Sheet</title>
<link href="https://fonts.googleapis.com/css2?family=Oswald:wght@500;600;700&family=Montserrat:wght@500;600;700&display=swap" rel="stylesheet">
<style>
  :root{
    --backdrop:#b3b3b3;
    --navy:#003a70;
    --coral:#ef6161;
    --coral-deep:#e2694a;
    --cream:#f7f3e6;
    --blush-top:#fbf0ee;
    --blush-bottom:#f9dfda;
    --ink:#111111;
    --white:#ffffff;
  }
  *{margin:0;padding:0;box-sizing:border-box}
  html,body{width:964px;height:1200px;overflow:hidden;background:var(--backdrop)}
  .sheet{position:absolute;left:172px;top:134px;width:620px;height:931px;background:#f5f5f5;overflow:hidden;font-family:'Montserrat',sans-serif;color:var(--ink)}
  .hero-art{position:absolute;left:0;top:0;width:620px;height:345px}
  .brand{position:absolute;left:30px;top:19px;display:flex;flex-direction:column;align-items:center;width:108px}
  .brand-mark{width:67px;height:55px;background:var(--navy)}
  .brand-name{margin-top:5px;font-family:'Oswald',sans-serif;font-weight:600;font-size:14px;line-height:15px;color:var(--navy);text-align:center;text-transform:uppercase}
  .headline{position:absolute;left:26px;top:128px;font-family:'Oswald',sans-serif;font-weight:700;color:var(--white);text-transform:uppercase;text-shadow:1px 2px 3px rgba(0,0,0,.25)}
  .headline span{display:block;white-space:nowrap;transform-origin:left center}
  .headline .line-1{font-size:66px;line-height:66px;transform:scaleX(.85)}
  .headline .line-2{font-size:58px;line-height:58px;transform:scaleX(.82)}
  .headline .line-3{font-size:61px;line-height:60px;transform:scaleX(.85)}
  .body-bg{position:absolute;left:0;top:342px;width:620px;height:414px;background:linear-gradient(var(--blush-top),var(--blush-bottom))}
  .features{position:absolute;left:0;top:361px;width:620px}
  .feature{position:absolute;width:150px;text-align:center}
  .feature-icon{width:60px;height:54px;margin:0 auto;display:flex;align-items:center;justify-content:center}
  .feature-icon.navy{background:var(--navy)}
  .feature-icon.coral{background:linear-gradient(var(--coral),var(--coral-deep))}
  .feature h3{margin-top:4px;font-family:'Oswald',sans-serif;font-weight:600;font-size:19px;line-height:24px}
  .feature p{font-size:11.5px;font-weight:600;line-height:14.5px}
  .rule{position:absolute;left:0;width:620px;border-top:1.5px dotted var(--navy)}
  .section-title{position:absolute;left:150px;width:320px;height:36px;background:linear-gradient(90deg,rgba(0,58,112,0),var(--navy) 30%,var(--navy) 70%,rgba(0,58,112,0));font-family:'Oswald',sans-serif;font-weight:600;font-size:26px;line-height:36px;color:var(--white);text-align:center}
  .product-slot{position:absolute;top:540px;width:109px;height:102px;background:var(--white);box-shadow:0 0 6px rgba(226,105,74,.25)}
  .offers{position:absolute;left:0;top:696px;width:620px;font-size:15px;font-weight:500}
  .offer{position:absolute;display:flex;align-items:center;gap:8px;white-space:nowrap}
  .tick{width:14px;height:14px;border-radius:50%;display:flex;align-items:center;justify-content:center}
  .tick.coral{background:var(--coral)}
  .tick.navy{background:var(--navy)}
  .partners{position:absolute;left:0;top:756px;width:620px;height:79px;background:var(--white)}
  .badge{position:absolute}
  .footer{position:absolute;left:0;top:835px;width:620px;height:96px;background:var(--navy);color:var(--white)}
  .footer-divider{position:absolute;left:348px;top:0;height:96px;border-left:1.5px dotted var(--coral)}
  .cta{position:absolute;left:25px;top:16px}
  .cta h2{font-family:'Oswald',sans-serif;font-weight:600;font-size:29px;line-height:36px;white-space:nowrap;transform:scaleX(.86);transform-origin:left center}
  .cta p{font-size:13px;font-weight:500;line-height:16.5px}
  .contact{position:absolute;left:376px;top:10px}
  .contact-row{display:flex;align-items:center;gap:9px;white-space:nowrap}
  .phone{font-weight:700;font-size:26px;line-height:32px}
  .email{font-weight:500;font-size:15px;line-height:20px}
  .social{display:flex;gap:3px;margin-left:25px;margin-top:6px}
  .social span{width:20px;height:20px;border-radius:50%;background:var(--coral)}
</style>
</head>
<body>
<div class="sheet">
  <svg class="hero-art" viewBox="0 0 620 345">
    <defs>
      <linearGradient id="bandFill" x1="0" y1="0" x2="0" y2="1">
        <stop offset="0" stop-color="#ef6161"/>
        <stop offset="1" stop-color="#e2694a"/>
      </linearGradient>
      <linearGradient id="photoFill" x1="0" y1="0" x2="1" y2="1">
        <stop offset="0" stop-color="#f6d9ae"/>
        <stop offset="0.55" stop-color="#e9a35c"/>
        <stop offset="1" stop-color="#b9753a"/>
      </linearGradient>
    </defs>
    <path d="M482 0 L620 0 L620 120 L410 120 Q425 45 482 0 Z" fill="#003a70"/>
    <path d="M498 0 Q455 35 440 95" stroke="#f5f5f5" stroke-width="4" fill="none"/>
    <path d="M470 300 Q545 350 620 310 L620 290 L470 290 Z" fill="#003a70"/>
    <path d="M306 84 L620 84 L620 305 L490 305 C455 290 430 255 405 205 C385 165 360 110 306 84 Z" fill="url(#photoFill)" role="img" aria-label="Photo of a shirt hanging on a screen-printing press under warm lights"/>
    <path d="M0 124 L310 124 C350 124 375 150 395 190 C420 240 450 300 520 342 L0 342 Z" fill="url(#bandFill)" stroke="#f7f3e6" stroke-width="4"/>
  </svg>

  <div class="brand">
    <div class="brand-mark"></div>
    <div class="brand-name">Copper Hollow<br>Graphics</div>
  </div>

  <h1 class="headline">
    <span class="line-1">Order Shirts</span>
    <span class="line-2">For Your All Of</span>
    <span class="line-3">Your Retreats</span>
  </h1>

  <div class="body-bg"></div>

  <div class="features">
    <div class="feature" style="left:9px">
      <div class="feature-icon navy">
        <svg width="34" height="34" viewBox="0 0 34 34" fill="none" stroke="#fff" stroke-width="1.3"><path d="M6 14 L17 8 L28 14 L17 20 Z"/><path d="M6 18 L17 24 L28 18"/><path d="M6 22 L17 28 L28 22"/></svg>
      </div>
      <h3>Low Minimums</h3>
      <p>Order as few as 24<br>pieces to get started.</p>
    </div>
    <div class="feature" style="left:159px">
      <div class="feature-icon coral">
        <svg width="34" height="34" viewBox="0 0 34 34" fill="none" stroke="#fff" stroke-width="1.3"><path d="M8 6 L14 26"/><circle cx="15" cy="28" r="2"/><rect x="15" y="9" width="11" height="11" transform="rotate(-15 20 14)"/><path d="M3 16 H9 M4 20 H10 M5 24 H11"/></svg>
      </div>
      <h3>Fast Turnaround</h3>
      <p>2-week standard<br>delivery.</p>
    </div>
    <div class="feature" style="left:303px">
      <div class="feature-icon navy">
        <svg width="36" height="34" viewBox="0 0 36 34" fill="none" stroke="#fff" stroke-width="1.3"><circle cx="18" cy="9" r="4"/><path d="M11 28 V18 Q18 13 25 18 V28"/><circle cx="8" cy="11" r="3"/><circle cx="28" cy="11" r="3"/><path d="M3 26 V19 Q8 15 11 17 M33 26 V19 Q28 15 25 17"/></svg>
      </div>
      <h3>Real People</h3>
      <p>Work with our team<br>of experts and artists.</p>
    </div>
    <div class="feature" style="left:454px">
      <div class="feature-icon coral">
        <svg width="34" height="34" viewBox="0 0 34 34" fill="none" stroke="#fff" stroke-width="1.3"><path d="M17 5 L25 8 V15 Q25 21 17 24 Q9 21 9 15 V8 Z"/><path d="M13 14 L16 17 L21 11"/><path d="M5 27 Q12 24 17 28 Q22 30 29 25"/></svg>
      </div>
      <h3>Guaranteed</h3>
      <p>We promise accurate,<br>quality work.</p>
    </div>
  </div>

  <div class="rule" style="top:492px"></div>
  <div class="section-title" style="top:494px">Our Products</div>

  <div class="product-slot" style="left:24px"></div>
  <div class="product-slot" style="left:140px"></div>
  <div class="product-slot" style="left:256px"></div>
  <div class="product-slot" style="left:372px"></div>
  <div class="product-slot" style="left:488px"></div>

  <div class="rule" style="top:652px"></div>
  <div class="section-title" style="top:653px">We Offer</div>

  <div class="offers">
    <div class="offer" style="left:80px;top:0">
      <span class="tick coral"><svg width="8" height="8" viewBox="0 0 8 8"><path d="M1 4 L3.2 6 L7 1.8" stroke="#fff" stroke-width="1.4" fill="none"/></svg></span>Art Design
    </div>
    <div class="offer" style="left:220px;top:0">
      <span class="tick navy"><svg width="8" height="8" viewBox="0 0 8 8"><path d="M1 4 L3.2 6 L7 1.8" stroke="#fff" stroke-width="1.4" fill="none"/></svg></span>We Pay ALL Royalties to the Movement
    </div>
    <div class="offer" style="left:80px;top:28px">
      <span class="tick navy"><svg width="8" height="8" viewBox="0 0 8 8"><path d="M1 4 L3.2 6 L7 1.8" stroke="#fff" stroke-width="1.4" fill="none"/></svg></span>Free Shipping
    </div>
    <div class="offer" style="left:220px;top:28px">
      <span class="tick coral"><svg width="8" height="8" viewBox="0 0 8 8"><path d="M1 4 L3.2 6 L7 1.8" stroke="#fff" stroke-width="1.4" fill="none"/></svg></span>Many Options of Shirt Styles and Colors
    </div>
  </div>

  <div class="partners">
    <svg class="badge" style="left:60px;top:16px" width="46" height="46"><circle cx="23" cy="23" r="22" fill="#2f6b3a"/></svg>
    <svg class="badge" style="left:128px;top:17px" width="44" height="44"><circle cx="22" cy="22" r="21" fill="#d9343a"/></svg>
    <svg class="badge" style="left:196px;top:22px" width="94" height="36"><rect width="94" height="36" fill="#5b3f9b"/></svg>
    <svg class="badge" style="left:315px;top:24px" width="68" height="30"><ellipse cx="34" cy="15" rx="34" ry="15" fill="#3a3f93"/></svg>
    <svg class="badge" style="left:400px;top:15px" width="68" height="48"><rect width="68" height="48" rx="22" fill="#2f9a3c"/></svg>
    <svg class="badge" style="left:492px;top:16px" width="68" height="46"><rect width="68" height="46" rx="6" fill="#2d8fd4"/></svg>
  </div>

  <footer class="footer">
    <div class="cta">
      <h2>We’d love to work with you!</h2>
      <p>Contact Dana Whitfield to start your next<br>shirt order today.</p>
    </div>
    <div class="footer-divider"></div>
    <div class="contact">
      <div class="contact-row">
        <svg width="16" height="16" viewBox="0 0 16 16"><path d="M4 2 L6 5 L4.5 6.5 Q6 10 9.5 11.5 L11 10 L14 12 L12.5 14.5 Q5 13 1.5 4 Z" fill="#fff"/></svg>
        <span class="phone">555-014-2387</span>
      </div>
      <div class="contact-row">
        <svg width="16" height="12" viewBox="0 0 16 12"><rect x="1" y="1" width="14" height="10" fill="none" stroke="#fff" stroke-width="1.4"/><path d="M1 1 L8 7 L15 1" stroke="#fff" stroke-width="1.4" fill="none"/></svg>
        <span class="email">dana@chgtshirts.com</span>
      </div>
      <div class="social"><span></span><span></span><span></span></div>
    </div>
  </footer>
</div>
</body>
</html>
```